FREE BBQ for life if you win our business with your creative menu design

Looking for a 11x17 size menu. we are a full service BBQ restaurant. We have an upscale environment as well as up scale service. We offer 5 star dinning at a casual price. we are on route 84 and are proud of that. we offer the finest smoked meats. Specializing in smoked pork beef and bison. we have an old barn wood decor. we only use oak to smoke our meats. use a lot of tarnished metal as well as some string nail art. Looking for a menu that goes along our style. i have attached as many pictures as i could to give you a fill of how we do it out here.
PLEASE USE THE 11"X17" MENU TEMPLATE ATTACHED IN THE PROJECT BRIEF.
Target Market(s)
Cool people and there families.
Industry/Entity Type
Business
Requirements
Must have
- I have attached the Current menu we use. File brantlys menu pub. Those are all the Items. There will be some changes as we but together the new menu. The prices are changing. but that should be an easy change as we go.
Nice to have
- We are getting away from the lunch dinner menu and going to an all day menu. so rather than coming with toast or bun we will now be asking as an option. I have attached a menu i tried to make as a sample of how we will be doing it. new menu single page and new menu single page flame. These are ideas i had but could not really make it work. so use them as an idea of what we are looking for but be creative.

```html
<!DOCTYPE html>
<html lang="en">
<head>
<meta charset="utf-8">
<title>Fresh From the Grill – Menu</title>
<link rel="stylesheet" href="https://fonts.googleapis.com/css2?family=Bebas+Neue&family=Rye&family=Crimson+Text:wght@400;700&family=Alfa+Slab+One&family=Luckiest+Guy&display=swap">
<style>
:root{
  --wood-dark:#1c2a2c;
  --wood-mid:#2f4a4c;
  --panel:rgba(14,16,18,.62);
  --ink:#f3efe6;
  --accent:#ef7a2a;
  --flame:#f7a53a;
  --flame-deep:#c2361a;
  --title-dark:#5b1e12;
  --metal-light:#8a8580;
  --metal-dark:#4f4c49;
  --kids-blue:#2a8fd0;
  --app-blue:#1f5fa8;
  --app-orange:#ee6a1f;
}
*{margin:0;padding:0;box-sizing:border-box}
html,body{width:927px;height:1200px;overflow:hidden;background:#222}
.menu{
  position:relative;width:927px;height:1200px;overflow:hidden;
  background:
    repeating-linear-gradient(180deg,rgba(0,0,0,.35) 0 2px,transparent 2px 46px),
    linear-gradient(180deg,var(--wood-mid),var(--wood-dark) 40%,var(--wood-mid) 75%,var(--wood-dark));
  font-family:"Crimson Text",serif;color:var(--ink);
}
.tin-strip{position:absolute;left:0;right:0;bottom:0;height:30px;background:linear-gradient(90deg,#8c8c8a,#b5b3ae,#7d7c78,#a9a7a2)}
.decor{position:absolute}
.decor--metal-top{left:0;top:0;width:300px;height:230px;background:radial-gradient(ellipse at 35% 40%,var(--metal-light),var(--metal-dark) 70%,transparent 100%);opacity:.7}
.decor--sign-right{top:220px;width:200px;height:380px;background:linear-gradient(160deg,#3d6d9a,#a45a2c);border-radius:6px;transform:rotate(-6deg);right:-30px}
.decor--plate-left{left:-30px;top:290px;width:110px;height:360px;background:linear-gradient(180deg,#5e4c66,#7b6a7a);border-radius:40px}
.decor--plate-topright{right:0;top:70px;width:70px;height:80px;background:linear-gradient(135deg,#9a9a94,#5f5f5a)}
.decor--disc-top{right:60px;top:-50px;width:120px;height:100px;border-radius:50%;background:radial-gradient(#7a5a3e,#4a3526)}
.decor--disc-left{left:-50px;top:730px;width:100px;height:130px;border-radius:50%;background:radial-gradient(#7b4d2a,#3f2817)}
.decor--crate-right{right:-20px;top:660px;width:160px;height:460px;background:linear-gradient(180deg,#6a4a33,#4b3a4a);border-radius:10px}
.decor--metal-left{left:0;top:880px;width:70px;height:260px;background:linear-gradient(180deg,#7e7c78,#5c5b57)}

.title{position:absolute;left:314px;top:40px;width:500px;text-align:center}
.title__top{font-family:"Alfa Slab One",serif;font-size:34px;letter-spacing:1px;color:var(--title-dark);line-height:1}
.title__main{font-family:"Rye",serif;font-size:124px;letter-spacing:4px;line-height:.9;color:var(--flame);
  text-shadow:0 0 10px var(--flame-deep),0 0 22px rgba(230,80,20,.7)}

.panel{position:absolute;left:56px;top:214px;width:808px;height:946px;background:var(--panel);border-radius:10px}

.section{position:absolute}
.section__title{font-family:"Bebas Neue",sans-serif;font-size:47px;line-height:1;color:#fff;margin-bottom:9px}
.item{margin-bottom:11px;font-size:8.6px;line-height:1.45;width:210px}
.item__name{font-weight:700;color:var(--accent);font-size:9.2px}
.item__price{color:var(--ink);font-weight:400}
.intro{font-size:11.4px;line-height:1.4;width:232px;margin-bottom:12px}
.intro strong{font-size:12.4px}
.list{font-size:8.6px;line-height:1.5;list-style:none}

.sec--appetizer{left:86px;top:248px}
.sec--bison{left:86px;top:606px}
.sec--bison .item{width:235px}
.sec--smoked{left:355px;top:248px}
.sec--smoked-more{left:612px;top:296px}
.sec--desserts{left:355px;top:552px}
.sec--salads{left:355px;top:766px}
.sec--sides{left:355px;top:898px}
.sec--customs{left:612px;top:552px}
.sec--drinks{left:612px;top:838px}

.brand-row{display:flex;gap:16px;align-items:center;margin:6px 0 10px}
.brand{display:flex;align-items:center;gap:5px;font-weight:700;font-size:16px;color:#fff}
.brand__dot{width:18px;height:18px;border-radius:50%;background:#fff}

.kids-badge{position:absolute;left:80px;top:900px;width:130px;height:128px}
.kids-badge svg{position:absolute;left:0;top:0}
.kids-badge__text{position:absolute;left:0;top:18px;width:130px;text-align:center;font-family:"Luckiest Guy",sans-serif;color:#fff;line-height:1.05}
.kids-badge__text .l1{font-size:12px;background:var(--app-orange);display:inline-block;padding:2px 6px;transform:rotate(-5deg)}
.kids-badge__text .l2{font-size:22px;display:block;margin-top:4px}
.kids-badge__text .l3{font-size:17px;display:block;margin-top:6px}

.app{position:absolute;left:150px;top:990px;width:185px;height:150px}
.app__ring{position:absolute;left:34px;top:0;width:124px;height:124px;border-radius:50%;background:#fff;display:flex;align-items:center;justify-content:center}
.app__name{font-family:"Crimson Text",serif;font-weight:700;font-size:26px;color:var(--app-blue)}
.app__banner{position:absolute;left:0;top:90px;width:182px;background:var(--app-blue);color:#fff;font-family:"Bebas Neue",sans-serif;font-size:15px;text-align:center;padding:3px 0;transform:rotate(-2deg)}
.app__note{position:absolute;left:34px;top:114px;width:130px;background:var(--app-orange);color:#fff;font-size:8.4px;line-height:1.1;text-align:center;padding:3px 4px;transform:rotate(-2deg)}
</style>
</head>
<body>
<main class="menu">
  <div class="decor decor--metal-top" role="img" aria-label="Tarnished metal star ornament"></div>
  <div class="decor decor--disc-top" role="img" aria-label="Tarnished round metal plate"></div>
  <div class="decor decor--plate-topright" role="img" aria-label="Weathered metal plate"></div>
  <div class="decor decor--plate-left" role="img" aria-label="Tarnished embossed metal sign"></div>
  <div class="decor decor--disc-left" role="img" aria-label="Rusted round metal disc"></div>
  <div class="decor decor--metal-left" role="img" aria-label="Weathered tin sheets"></div>
  <div class="decor decor--sign-right" role="img" aria-label="String and nail art BBQ sign on blue board"></div>
  <div class="decor decor--crate-right" role="img" aria-label="Rustic painted wooden crate lettering"></div>
  <div class="tin-strip"></div>

  <header class="title">
    <div class="title__top">FRESH FROM THE</div>
    <div class="title__main">GRILL</div>
  </header>

  <div class="panel"></div>

  <section class="section sec--appetizer">
    <h2 class="section__title">APPETIZER</h2>
    <div class="item"><div class="item__name">King Rings</div>Green Chili battered fried golden crispy 1" thick onion rings. 7.89</div>
    <div class="item"><div class="item__name">Deep Fried Pickles</div>Crisp dill pickle chips battered and fried to a golden crispy brown. 7.89</div>
    <div class="item"><div class="item__name">Fried Okra</div>Okra is breaded then fried until golden. 7.89</div>
    <div class="item"><div class="item__name">Green Chili Waffle Fries</div>Crispy waffle-cut Fries, topped with a savory blend of cheese, and New Mexico green chile. 7.89</div>
    <div class="item"><div class="item__name">KC Wild Wings</div>Big, meaty pork wings, deep fried to a perfect golden brown, tossed in a hot and tangy Buffalo-style sauce, and served with spicy buttermilk ranch dressing on the side. 9.99</div>
    <div class="item"><div class="item__name">Sampler Platter</div>Two KC Wild Wings, 6oz Fried Pickles, 3 King Rings. 8.99</div>
  </section>

  <section class="section sec--bison">
    <h2 class="section__title">BISON</h2>
    <p class="intro"><strong>Heart Healthy</strong><br>Comes with 1 side dish and your choice of Texas toast, Kaiser bun, Whole wheat bread or Glutton Free bread</p>
    <div class="item"><div class="item__name">Bison Burger</div>Smoked then grilled served with pepper jack cheese lettuce tomato pickle toped with spicy ranch. 12.59</div>
    <div class="item"><div class="item__name">Bison Brisket</div>The belly of beast, smoked then sliced thin and grilled. Juicy and tender 18.65</div>
    <div class="item"><div class="item__name">Bison Steak</div>12oz of lean healthy meat cooked to your desired temp. 34.56</div>
  </section>

  <section class="section sec--smoked">
    <h2 class="section__title">SMOKED</h2>
    <div class="item"><div class="item__name">Baby Back Ribs</div>Tender to the bone, finger licking good, never need a knife, best ribs you'll ever have.<br>Full Rack 19.96 &nbsp;&nbsp; Half Rack 11.49</div>
    <div class="item"><div class="item__name">St. Louis Ribs</div>A nice big tender spare rib, slow smoked to tender that you can sink your teeth into.<br>Full Rack 30.98 &nbsp;&nbsp; Half Rack 16.45</div>
    <div class="item"><div class="item__name">Beef Brisket</div>The most insane mouth watering smoky, moist, succulent piece of meat your mouth will ever have. 10.95</div>
    <div class="item"><div class="item__name">Pulled Pork</div>Smoked for 18-20 hrs. then pulled and mixed with our signature base barbeque sauce.<br>9.59</div>
  </section>

  <section class="section sec--smoked-more">
    <div class="item"><div class="item__name">Sliced Pork</div>Smoked juicy tenderloin sliced thin then grilled per order. 9.54</div>
    <div class="item"><div class="item__name">Smoked Turkey</div>Breast meat smoked and sliced. Juicy and tender. 9.49</div>
    <div class="item"><div class="item__name">Smoked Chicken half</div>Moist and juicy smoked Breast and thigh on the bone basted with our signature sauce on the grill. 13.59</div>
    <div class="item"><div class="item__name">Rib Eye</div>12oz juicy steak grilled to your desired temp 21.95</div>
  </section>

  <section class="section sec--desserts">
    <h2 class="section__title">DESSERTS</h2>
    <div class="item"><div class="item__name">Peach Cobbler &amp; Ice Cream</div>Served hot topped with ice cream<br>Small 3.89 &nbsp;&nbsp; Large 5.89</div>
    <div class="item"><div class="item__name">Cookies A-L-Mode</div>2 hot gooey cookies topped with ice cream your choice chocolate chip or macadamia nut<br>Small 3.89 &nbsp;&nbsp; Large 5.89</div>
    <div class="item"><div class="item__name">Dessert of the week</div>Ask your server for our special dessert of the week</div>
  </section>

  <section class="section sec--salads">
    <h2 class="section__title">SALADS</h2>
    <div class="item"><div class="item__name">All You Can Eat Salad <span class="item__price">&nbsp; 7.89</span></div>Side Salad 3.00 &nbsp;&nbsp; With Meal 1.50</div>
    <div class="item"><div class="item__name">Add Meat To Your Salad</div>Choose from any sliced meat. 3.00</div>
  </section>

  <section class="section sec--sides">
    <h2 class="section__title">SIDE DISHES</h2>
    <ul class="list">
      <li>Green Chile Creamed Corn</li><li>Potato Salad</li><li>Baked Potato</li><li>Grilled Veggies</li><li>Baked Beans</li><li>Waffle Fries</li><li>Extra side 2.29</li>
    </ul>
  </section>

  <section class="section sec--customs">
    <h2 class="section__title">BB CUSTOMS</h2>
    <div class="item"><div class="item__name">BBQ Tacos</div>Three Tacos in blue and red shells with your choice of meat topped with shredded lettuce and Pico-D –BBQ and Spicy ranch.<br>(Excludes ribs and bison. ) 9.89</div>
    <div class="item"><span class="item__name">Taco Tuesday</span> is a Must! 5.00 tacos all day</div>
    <div class="item"><div class="item__name">Rowdy Chicken Sandwich</div>Skinless boneless chicken breasts breaded fried, topped with pepper jack cheese, lettuce, tomato onion and pickles. On a buttery grilled Texas toast. 10.59</div>
    <div class="item"><div class="item__name">Create Your Own Wrap</div>Pick your own meat, cheese, the additionals and sauce.</div>
  </section>

  <section class="section sec--drinks">
    <h2 class="section__title">DRINKS</h2>
    <div class="item"><div class="item__name">Lemonade</div>Regular, Strawberry, Watermelon Cherry, Peach 2.59</div>
    <div class="item__name">Fountain</div>
    <div class="brand-row">
      <span class="brand"><span class="brand__dot"></span>Fizzco</span>
      <span class="brand">Doc Fizz</span>
    </div>
    <div class="item">Fizzco, Doc Fizz, Root Beer, Lemon Mist, Mountain Zing, Diet Fizzco, Diet Doc Fizz 1.89</div>
    <div class="item"><div class="item__name">Iced Teas</div>Sweetened, Unsweetened 1.89</div>
  </section>

  <div class="kids-badge">
    <svg width="130" height="128" viewBox="0 0 130 128" aria-hidden="true">
      <polygon points="65,2 124,32 124,96 65,126 6,96 6,32" fill="var(--kids-blue)"/>
    </svg>
    <div class="kids-badge__text">
      <span class="l1">KIDS UNDER 4</span>
      <span class="l2">EAT FREE!</span>
      <span class="l3">SEE KIDS MENU</span>
    </div>
  </div>

  <div class="app">
    <div class="app__ring"><span class="app__name">Roostly</span></div>
    <div class="app__banner">JOIN OUR CUSTOMER LOYALTY APP</div>
    <div class="app__note">Get FREE FOOD when you become a loyal customer.</div>
  </div>
</main>
</body>
</html>
```